Qvx Brightforge Website

All the descriptions are available in the attached file. The designer has to structure the website and find the right images and icons. The website should look modern and avoid using images of real humans rather use animated images. Please note that the design should include home page, all the 4 services page , the contact us would be at the bottom of home page.

```html
<!DOCTYPE html>
<html lang="en">
<head>
<meta charset="utf-8">
<title>Qvx Brightforge</title>
<link href="https://fonts.googleapis.com/css2?family=Poppins:wght@400;500;600;700;800&family=Nunito+Sans:wght@400;600&display=swap" rel="stylesheet">
<style>
:root{
  --brand:#4a63b5;
  --ink:#111111;
  --text:#2b2b2b;
  --hero:#dbeaf2;
  --band:#eceff8;
  --white:#ffffff;
  --line:#9a9a9a;
}
*{box-sizing:border-box;margin:0;padding:0}
html,body{width:1200px;height:2684px;overflow:hidden;background:var(--white)}
body{position:relative;font-family:"Nunito Sans",sans-serif;color:var(--text)}
.abs{position:absolute}
.btn{position:absolute;background:var(--brand);color:var(--white);font-family:"Poppins",sans-serif;font-weight:600;font-size:17px;display:flex;align-items:center;justify-content:center;border-radius:2px;box-shadow:3px 4px 6px rgba(0,0,0,.18)}
.accent{color:var(--brand)}

/* header */
.site-header{position:absolute;left:0;top:0;width:1200px;height:86px;background:var(--white);z-index:3}
.brand-name{position:absolute;left:97px;top:26px;font-family:"Poppins",sans-serif;font-weight:700;font-size:24px;color:var(--brand);display:flex;align-items:center;gap:10px}
.brand-name i{width:14px;height:14px;background:var(--brand);display:block}
.nav a{position:absolute;top:30px;font-family:"Poppins",sans-serif;font-size:16px;color:#222;text-decoration:none}
.nav a.active{color:var(--brand);font-weight:600;border-bottom:2px solid var(--brand);padding-bottom:2px}

/* hero */
.hero-bg{position:absolute;left:0;top:86px}
.hero-title{left:99px;top:218px;font-family:"Poppins",sans-serif;font-weight:800;font-size:54px;line-height:56px;color:var(--ink);width:520px}
.hero-copy{left:99px;top:337px;font-size:16px;line-height:31px;color:#222}
.hero-art{left:420px;top:120px;width:640px;height:560px;border-radius:40% 30% 40% 30%;background:radial-gradient(ellipse at 55% 50%,#3d6fd1 0%,#8fbde8 45%,rgba(219,234,242,0) 72%)}
.dots span{position:absolute;left:45px;width:10px;height:10px;border-radius:50%;background:#8a8a8a}

/* about */
.about-art{left:0;top:815px;width:553px;height:428px;background:radial-gradient(ellipse at 50% 55%,#9cc6ec 0%,#cfe4f6 55%,#eef5fb 100%)}
.section-h{font-family:"Poppins",sans-serif;font-weight:700;font-size:32px;color:var(--ink)}
.about-copy{left:586px;top:866px;width:520px;font-size:15.5px;line-height:31px;color:#222}

/* services */
.services-band{left:0;top:1333px;width:1200px;height:627px;background:var(--band)}
.service-card{position:absolute;top:1459px;width:316px;height:424px;background:var(--white);text-align:center}
.service-card .art{position:absolute;left:60px;top:18px;width:196px;height:160px;border-radius:12px;background:linear-gradient(160deg,#e3eefb,#9fbde6)}
.service-card h3{position:absolute;left:0;right:0;top:212px;font-family:"Poppins",sans-serif;font-weight:600;font-size:18px;color:var(--ink)}
.service-card p{position:absolute;left:16px;right:16px;top:244px;font-size:15.5px;line-height:30px;color:#222}
.service-card a{position:absolute;left:0;right:0;top:376px;font-family:"Poppins",sans-serif;font-weight:600;font-size:17px;color:var(--brand);text-decoration:underline}
.arrow{position:absolute;top:1657px;width:28px;height:28px;border-radius:50%;background:#e2e4ea}

/* contact */
.field{position:absolute;left:98px;width:558px;height:48px;border:1px solid #9a9a9a;border-radius:3px;background:var(--white);padding:15px 18px;font-size:15.5px;color:#222}
.info-icon{position:absolute;left:734px;width:57px;height:42px;background:var(--brand);display:flex;align-items:center;justify-content:center}
.info-label{position:absolute;left:808px;font-family:"Poppins",sans-serif;font-weight:600;font-size:17px;color:var(--ink)}
.info-text{position:absolute;left:808px;font-size:15.5px;line-height:34px;color:#222}

/* footer */
.site-footer{left:0;top:2496px;width:1200px;height:188px;background:var(--band)}
.footer-brand{left:104px;top:2568px;font-family:"Poppins",sans-serif;font-weight:700;font-size:30px;color:var(--brand);display:flex;align-items:center;gap:12px}
.footer-brand i{width:18px;height:18px;background:var(--brand);display:block}
.footer-nav a{position:absolute;top:2555px;font-size:16px;color:#222;text-decoration:none}
.copyright{left:747px;top:2592px;font-size:16px;color:#222}
</style>
</head>
<body>

<header class="site-header">
  <div class="brand-name"><i></i>Qvx Brightforge</div>
  <nav class="nav">
    <a class="active" style="left:581px">Home</a>
    <a style="left:676px">Services</a>
    <a style="left:782px">Products</a>
    <a style="left:892px">Blog</a>
  </nav>
  <div class="btn" style="left:964px;top:17px;width:137px;height:51px">Contact Us</div>
</header>

<svg class="hero-bg" width="1200" height="700" viewBox="0 86 1200 700" aria-hidden="true">
  <polygon points="0,86 1194,86 300,630 0,700" fill="#dbeaf2"/>
  <path d="M0,700 C150,640 300,615 450,640 C650,680 800,760 980,750 C1080,745 1150,715 1200,690 L1200,86 L1194,86 L300,630 L0,700 Z" fill="#dbeaf2" opacity="0"/>
  <path d="M0,690 C170,625 320,610 470,640 C660,680 820,760 990,752 C1090,748 1160,712 1200,688" fill="none" stroke="#c9cfd9" stroke-width="10"/>
</svg>
<div class="abs hero-art" role="img" aria-label="Isometric illustration of a team building software on a large monitor with keyboard and colourful blocks"></div>
<div class="dots"><span style="top:321px;background:var(--brand)"></span><span style="top:341px"></span><span style="top:362px"></span></div>
<h1 class="abs hero-title">Welcome To <span class="accent">Qvx Brightforge</span></h1>
<p class="abs hero-copy">Empower your digital journey with our advanced IT solutions.<br>From data to web and mobile apps, we've got you covered.</p>
<div class="btn" style="left:99px;top:412px;width:137px;height:52px">Get Started</div>

<div class="abs about-art" role="img" aria-label="Illustration of two colleagues working at a desk with a monitor showing charts"></div>
<h2 class="abs section-h" style="left:586px;top:812px">About <span class="accent">Us</span></h2>
<p class="abs about-copy">We are a forward-thinking IT consulting firm specializing in providing cutting-edge data analytics, web application development, and mobile app development services. Our passion for innovation and technology drives us to deliver tailor-made solutions that empower businesses to thrive in the digital landscape.We take pride in our ability to collaborate with early-stage startups as their technology partner, helping them navigate the challenges of launching and scaling their ventures. Our team of experienced professionals works closely with clients, understanding their unique requirements and goals, to craft bespoke solutions that propel growth and foster success.</p>
<div class="btn" style="left:586px;top:1191px;width:136px;height:51px">Read More</div>

<div class="abs services-band"></div>
<h2 class="abs section-h" style="left:0;width:1200px;text-align:center;top:1390px">Our <span class="accent">Services</span></h2>
<div class="arrow" style="left:38px"><svg width="28" height="28"><path d="M16,9 L11,14 L16,19" fill="none" stroke="#999" stroke-width="1.6"/></svg></div>
<div class="arrow" style="left:1135px"><svg width="28" height="28"><path d="M12,9 L17,14 L12,19" fill="none" stroke="#222" stroke-width="1.6"/></svg></div>

<article class="service-card" style="left:99px">
  <div class="art" role="img" aria-label="Illustration of people working with data dashboards and charts"></div>
  <h3>Data Analytics</h3>
  <p>At Qvx Brightforge, our proficiency consists of linking your leadership team's objectives with the relevant data that holds significance.</p>
  <a>Read More</a>
</article>
<article class="service-card" style="left:442px">
  <div class="art" role="img" aria-label="Illustration of web development tools, code windows and devices"></div>
  <h3>Web Development</h3>
  <p>At Qvx Brightforge, we are a trailblazing web development company committed solutions that empower businesses to the ever-evolving online landscape.</p>
  <a>Read More</a>
</article>
<article class="service-card" style="left:785px">
  <div class="art" role="img" aria-label="Illustration of a team building a mobile app on a large phone screen"></div>
  <h3>Mobile App Development</h3>
  <p>At Qvx Brightforge, we are a pioneering mobile app development company experiences that captivate and engage various platforms.</p>
  <a>Read More</a>
</article>

<h2 class="abs section-h" style="left:99px;top:2024px">Contact <span class="accent">Us</span></h2>
<div class="field" style="top:2088px">Name</div>
<div class="field" style="top:2148px">Email</div>
<div class="field" style="top:2208px">Phone Number</div>
<div class="field" style="top:2266px;height:87px">Message</div>
<div class="btn" style="left:98px;top:2376px;width:137px;height:51px">Submit</div>

<div class="info-icon" style="top:2099px"><svg width="18" height="22" viewBox="0 0 18 22"><path d="M9,1 C4.5,1 1.5,4.3 1.5,8.3 C1.5,13.5 9,21 9,21 C9,21 16.5,13.5 16.5,8.3 C16.5,4.3 13.5,1 9,1 Z" fill="#fff"/><circle cx="9" cy="8.3" r="3" fill="#4a63b5"/></svg></div>
<div class="info-label" style="top:2094px">Address:</div>
<div class="info-text" style="top:2123px">Suite 12/48 Harbourline Avenue,<br>Eastvale WA 6210</div>

<div class="info-icon" style="top:2214px"><svg width="20" height="20" viewBox="0 0 20 20"><path d="M4,1 L7.5,1 L9,6 L6.8,7.6 C7.8,10 10,12.2 12.4,13.2 L14,11 L19,12.5 L19,16 C19,17.8 17.6,19 16,19 C7.5,18.5 1.5,12.5 1,4 C1,2.4 2.2,1 4,1 Z" fill="#fff"/></svg></div>
<div class="info-label" style="top:2209px">Phone:</div>
<div class="info-text" style="top:2238px">+61 (08) 5550 2741 (Sales / Support)</div>

<div class="info-icon" style="top:2298px"><svg width="20" height="15" viewBox="0 0 20 15"><rect x="0" y="0" width="20" height="15" rx="1.5" fill="#fff"/><path d="M1,1.5 L10,8.5 L19,1.5" fill="none" stroke="#4a63b5" stroke-width="1.6"/></svg></div>
<div class="info-label" style="top:2293px">Email:</div>
<div class="info-text" style="top:2322px">dev@qvxbrightforge.example</div>

<footer class="abs site-footer"></footer>
<div class="abs footer-brand"><i></i>Qvx Brightforge</div>
<nav class="footer-nav">
  <a style="left:648px">Home</a>
  <a style="left:737px">Services</a>
  <a style="left:843px">Products</a>
  <a style="left:952px">Blog</a>
  <a style="left:1023px">Contact Us</a>
</nav>
<p class="abs copyright">Copyrights@2023.Qvx Brightforge.All Rights Reserved</p>

</body>
</html>
```